PixelHarbor Rangers (Ledgerline Nova)
A website dedicated to crypto education. We are a new company focused on blockchain edutainment (education and interesting and entertaining content about the blockchain space). We want a fun, clean/minimalist and modern website that is made up of an education platform which could be a website in it’s own right. It will be the reference point for our users/community for all of our other blockchain based content in the PHR website ecosystem which will be covering; crypto news, digital asset investing (including a technical and fundamental analysis subscription service), blockchain business solutions and an NFT section that will cover creative art projects (art, music, gaming and more). To feature a logins and payment system which may need a shopping basket set up for tutorial/educational platform that is accessed via the website, NFT page with sub-categories: education and NFT and metaverse/virtual world and merchandise shopping page which is Web 3.0 enabled (able to link to a VeloPurse, Kindle Vault etc , digital asset education page featuring blog and newsletter subscriptions links, A social media page where people can access videos, podcasts and our presence on other platforms such as Chirplo, Snapmora, Huddlex, Wirepost etc.
Number of Pages Required
5+ page
Look and feel

```html
<!DOCTYPE html>
<html lang="en">
<head>
<meta charset="utf-8">
<title>PixelHarbor Rangers – Home, light and dark themes</title>
<link rel="stylesheet" href="https://fonts.googleapis.com/css2?family=Poppins:wght@300;400;500;600;700;800&display=swap">
<style>
:root{
  --board:#c9cacd;
  --navy:#0d2a5c;
  --red:#a50f13;
  --teal:#179a8b;
  --ink:#1d1d1f;
  --muted:#5b5f66;
  --white:#ffffff;
  --hero-band:rgba(24,52,112,.82);
}
*{box-sizing:border-box;margin:0;padding:0}
html,body{width:754px;height:1200px;overflow:hidden;background:var(--board)}
body{position:relative;font-family:'Poppins',sans-serif}

.theme-light{
  --bg:#ffffff; --title:var(--navy); --text:var(--muted); --head:var(--ink);
  --card:#ffffff; --card-line:#e3e5e9; --hl-bg:#ffffff; --hl-line:#d5d8de; --hl-title:var(--red);
  --eco-title:var(--red); --tut-bg:#eef0f3; --tut-title:var(--navy); --tut-text:var(--ink);
  --price:var(--red); --news-btn:var(--teal); --input-line:#d4d7dc; --foot-bg:#ffffff; --foot-line:#e6e7ea;
}
.theme-dark{
  --bg:#000000; --title:#ffffff; --text:#d9dbe0; --head:#ffffff;
  --card:#121315; --card-line:#1d1e21; --hl-bg:#0d2a5c; --hl-line:#ffffff; --hl-title:#ffffff;
  --eco-title:#ffffff; --tut-bg:#0a2358; --tut-title:#ffffff; --tut-text:#ffffff;
  --price:#ffffff; --news-btn:var(--navy); --input-line:#ffffff; --foot-bg:#000000; --foot-line:#3a3b3f;
}

.panel{position:absolute;top:22px;width:353px;height:1160px;overflow:hidden;background:var(--bg);
  display:flex;flex-direction:column;box-shadow:0 1px 4px rgba(0,0,0,.25)}
.panel--left{left:17px}
.panel--right{left:387px}
.panel section,.panel footer,.panel header,.panel .bottom-bar{position:relative;flex:none;width:100%}

/* hero */
.hero{height:216px;color:var(--white)}
.hero-photo{position:absolute;inset:0;background:linear-gradient(180deg,#151619 0%,#24262d 45%,#2a3550 80%,#1f2b4a 100%)}
.logo{position:absolute;left:33px;top:9px;font-size:7px;font-weight:700}
.account{position:absolute;right:34px;top:6px;display:flex;gap:6px;font-size:4.2px;align-items:center}
.account span{display:flex;align-items:center;gap:3px}
.ring{width:11px;height:11px;border:.6px solid #fff;border-radius:50%;display:inline-flex;align-items:center;justify-content:center}
.rule{position:absolute;left:33px;right:34px;top:25px;height:.6px;background:rgba(255,255,255,.35)}
.rule::before{content:"";position:absolute;left:0;top:-.3px;width:44px;height:1.2px;background:var(--red)}
.nav{position:absolute;left:35px;top:33px;display:flex;gap:6px;font-size:4.2px;line-height:6px}
.nav i{font-style:normal;opacity:.8}
.socials{display:flex;gap:3px;font-size:3.4px;line-height:5px;align-items:center}
.hero .socials{position:absolute;right:34px;top:34px;color:#fff}
.hero-band{position:absolute;left:0;right:0;top:171px;height:45px;background:var(--hero-band)}
.hero-title{position:absolute;left:32px;top:5px;font-size:13.5px;line-height:18px;font-weight:700}
.hero-sub{position:absolute;left:33px;top:24px;font-size:3.9px;line-height:9px;width:148px}
.btn{display:inline-flex;align-items:center;justify-content:center;border-radius:9px;font-weight:700;font-size:4.4px;color:#fff;height:16px}
.btn--red{background:var(--red)}
.btn--line{border:.7px solid rgba(255,255,255,.85)}
.hero-actions{position:absolute;left:195px;top:13px;display:flex;gap:3px}
.hero-actions .btn--red{width:57px}.hero-actions .btn--line{width:65px}
.arrow{position:absolute;top:20px;width:10px;height:6px}
.arrow--prev{left:10px}.arrow--next{right:10px}

.sec-title{position:absolute;left:0;right:0;text-align:center;font-size:12px;line-height:16px;color:var(--title);font-weight:400}
.sec-title b{font-weight:700}
.sec-text{position:absolute;left:50%;transform:translateX(-50%);text-align:center;font-size:3.9px;line-height:9px;color:var(--text)}

/* ecosystem */
.ecosystem{height:174px}
.ecosystem .sec-title{top:20px}
.ecosystem .sec-text{top:40px;width:215px}
.eco-row{position:absolute;left:27px;top:69px;display:flex;width:300px}
.eco-item{width:75px;height:80px;display:flex;flex-direction:column;align-items:center;text-align:center;padding-top:6px}
.eco-item svg{width:24px;height:24px;stroke:var(--title)}
.eco-item h3{font-size:4.3px;font-weight:600;color:var(--eco-title);margin-top:5px;line-height:7px}
.eco-item p{font-size:3.5px;line-height:7px;color:var(--text);margin-top:2px;width:64px}
.eco-item--active{background:var(--hl-bg);border:.8px solid var(--hl-line);border-radius:8px;box-shadow:0 1px 4px rgba(0,0,0,.12)}
.eco-item--active h3{color:var(--hl-title)}
.theme-dark .eco-item--active p{color:#fff}
.round-arrow{position:absolute;top:97px;width:10px;height:10px;border:.6px solid var(--title);border-radius:50%}
.round-arrow svg{width:100%;height:100%;stroke:var(--title);display:block}
.round-arrow--prev{left:15px}.round-arrow--next{right:16px}
.pixel-art{position:absolute}

/* education */
.education{height:126px;color:#fff}
.edu-photo{position:absolute;inset:0;background:linear-gradient(160deg,#2a4f8f 0%,#22467f 50%,#1d3c70 100%)}
.education .sec-title{top:24px;color:#fff}
.education .sec-text{top:47px;width:255px;color:#e8ecf3;font-size:4.3px;line-height:10px}
.edu-actions{position:absolute;left:125px;top:80px;display:flex;gap:2px}
.edu-actions .btn{width:57px;height:17px}

/* nft */
.nft{height:212px}
.nft .sec-title{top:24px}
.nft .sec-text{top:45px;width:215px}
.nft-row{position:absolute;left:33px;top:70px;display:flex;gap:10px}
.nft-card{width:89px;height:112px;background:var(--card);border:.7px solid var(--card-line);box-shadow:0 1px 3px rgba(0,0,0,.1);padding:2px}
.nft-media{height:47px}
.nft-card h3{font-size:4.3px;line-height:6px;font-weight:500;color:var(--head);margin:9px 0 0 5px}
.nft-card p{font-size:3.6px;line-height:7.5px;color:var(--text);margin:2px 5px 0}
.btn--navy{background:var(--navy);width:41px;height:11px;border-radius:6px;font-size:3.6px;font-weight:500;margin:4px 0 0 5px}

/* tutorial */
.tutorial{height:184px;background:var(--tut-bg)}
.tutorial .sec-title{top:17px;color:var(--tut-title);font-weight:500}
.tut-row{position:absolute;left:33px;top:42px;display:flex;gap:4px}
.tut-card{width:93px;color:var(--tut-text)}
.tut-media{position:relative;height:72px;box-shadow:0 1px 3px rgba(0,0,0,.25)}
.play{position:absolute;left:50%;top:50%;width:14px;height:14px;margin:-7px 0 0 -7px;border-radius:50%;background:#fff}
.play::after{content:"";position:absolute;left:5.5px;top:4px;border-left:4.5px solid #222;border-top:3px solid transparent;border-bottom:3px solid transparent}
.tut-card h3{font-size:4.5px;font-weight:500;line-height:8px;margin-top:8px}
.tut-card p{font-size:3.5px;line-height:7.5px;color:var(--text);margin-top:2px}
.theme-dark .tut-card p{color:#d9dfeb}
.tut-meta{display:flex;justify-content:space-between;align-items:center;margin-top:5px;font-size:4.4px;line-height:6px;color:var(--price)}
.tut-meta s{opacity:.5;font-size:4px}
.tut-card .socials{color:var(--tut-text);gap:2px;font-size:3px}

/* newsletter */
.newsletter{height:111px}
.newsletter .sec-title{top:22px;color:var(--head);font-weight:600}
.newsletter .sec-text{top:44px;width:170px}
.news-form{position:absolute;left:64px;top:66px;display:flex;gap:5px}
.news-input{width:152px;height:21px;border:.8px solid var(--input-line);border-radius:11px;background:#fff;font-size:4px;color:#333;display:flex;align-items:center;padding-left:9px}
.news-btn{width:68px;height:21px;background:var(--news-btn);border-radius:11px;color:#fff;font-size:5.5px;font-weight:700;display:flex;align-items:center;justify-content:center}

/* footer */
.site-footer{height:107px;background:var(--foot-bg);border-top:.6px solid var(--foot-line)}
.foot-col{position:absolute;top:21px;font-size:3.7px;line-height:9px;color:var(--head)}
.foot-col h4{font-size:4.3px;font-weight:600;line-height:6px;margin-bottom:9px;position:relative}
.foot-col h4::after{content:"";position:absolute;left:0;bottom:-5px;width:9px;height:.7px;background:var(--muted)}
.foot-col p{margin:0}
.foot-col .label{font-weight:600;font-size:4px;line-height:7px;margin-top:2px}
.foot-col .line{line-height:7px;display:flex;gap:2px;align-items:flex-start}
.foot-col .line svg{flex:none;width:4px;height:4px;margin-top:1.5px;fill:var(--head)}
.foot-col--links{left:33px}.foot-col--eco{left:82px}.foot-col--contact{left:155px;width:80px}.foot-col--news{left:240px;width:84px}
.foot-input{margin-top:5px;width:83px;height:12px;border:.6px solid var(--input-line);border-radius:6px;display:flex;align-items:center;justify-content:space-between;padding:0 3px 0 6px;font-size:3.4px}
.foot-input i{width:6px;height:6px;border-radius:50%;background:var(--red)}
.theme-dark .foot-input i{background:#fff}
.bottom-bar{height:30px;background:var(--foot-bg);border-top:.6px solid var(--foot-line);color:var(--head)}
.copyright{position:absolute;left:34px;top:11px;font-size:4px;line-height:6px}
.pay-row{position:absolute;left:148px;top:11px;display:flex;gap:2px}
.pay-row span{width:11px;height:7px;background:#e6ecf5;border:.4px solid #b9c3d3;font-size:2px;display:flex;align-items:center;justify-content:center;color:#1d2b4a}
.bottom-bar .socials{position:absolute;right:36px;top:12px;color:var(--head)}
</style>
</head>
<body>

<main class="panel panel--left theme-light">
  <header class="hero">
    <div class="hero-photo" role="img" aria-label="Photo of a smiling man in glasses and a denim jacket working at a laptop in a café"></div>
    <div class="logo">PixelHarbor Rangers</div>
    <div class="account">
      <span><i class="ring"><svg width="5" height="5" viewBox="0 0 10 10" fill="#fff"><circle cx="5" cy="3" r="2"/><path d="M1 10c0-3 2-4 4-4s4 1 4 4z"/></svg></i>LOGIN</span>
      <span><i class="ring"><svg width="5" height="5" viewBox="0 0 10 10" fill="#fff"><path d="M0 1h2l1 5h6l1-4H3"/><circle cx="4" cy="8.5" r="1"/><circle cx="8" cy="8.5" r="1"/></svg></i>CART</span>
    </div>
    <div class="rule"></div>
    <nav class="nav"><span>HOME</span><i>|</i><span>ABOUT US</span><i>|</i><span>PHR ECOSYSTEM</span><i>|</i><span>BLOG</span><i>|</i><span>CONTACT</span></nav>
    <div class="socials"><span>Chirplo</span><span>Snapmora</span><span>Huddlex</span><span>Wirepost</span></div>
    <div class="hero-band">
      <svg class="arrow arrow--prev" viewBox="0 0 10 6" fill="none" stroke="#fff" stroke-width="1"><path d="M10 3H1M3 1L1 3l2 2"/></svg>
      <h1 class="hero-title">PixelHarbor Rangers</h1>
      <p class="hero-sub">Lorem ipsum dolor sit amet, consectetur adipiscing elit, sed do eiusmod tempor incididunt ut labore et dolore magna aliqua.</p>
      <div class="hero-actions"><span class="btn btn--red">GET STARTED</span><span class="btn btn--line">CHECK YOUR RESULT</span></div>
      <svg class="arrow arrow--next" viewBox="0 0 10 6" fill="none" stroke="#fff" stroke-width="1"><path d="M0 3h9M7 1l2 2-2 2"/></svg>
    </div>
  </header>

  <section class="ecosystem">
    <h2 class="sec-title"><b>PHR</b> Ecosystem</h2>
    <p class="sec-text">Lorem ipsum dolor sit amet, consectetur adipiscing elit, sed do eiusmod tempor incididunt ut labore et dolore magna aliqua. Ut enim ad minim veniam, quis nostrud</p>
    <span class="round-arrow round-arrow--prev"><svg viewBox="0 0 10 10" fill="none" stroke-width=".8"><path d="M6 3L4 5l2 2"/></svg></span>
    <div class="eco-row">
      <div class="eco-item"><svg viewBox="0 0 24 24" fill="none" stroke-width=".9"><circle cx="11" cy="10" r="7"/><circle cx="11" cy="10" r="4.5"/><circle cx="15" cy="16" r="5"/><path d="M13 18l4-4"/></svg><h3>Crypto News</h3><p>Lorem ipsum dolor sit consectetur adipiscing elit, sed do eiusmod tempor incididunt ut</p></div>
      <div class="eco-item eco-item--active"><svg viewBox="0 0 24 24" fill="none" stroke-width=".9"><rect x="2" y="5" width="15" height="12"/><path d="M4 15v-3M7 15v-5M10 15v-4M4 10l4-3 3 2 5-4"/><circle cx="17" cy="16" r="4"/><circle cx="17" cy="16" r="2"/></svg><h3>Digital asset investing</h3><p>Lorem ipsum dolor sit consectetur adipiscing elit, sed do eiusmod tempor incididunt ut</p></div>
      <div class="eco-item"><svg viewBox="0 0 24 24" fill="none" stroke-width=".9"><path d="M12 2l4 2v4l-4 2-4-2V4z"/><path d="M6 12l4 2v4l-4 2-4-2v-4z"/><path d="M18 12l4 2v4l-4 2-4-2v-4z"/><path d="M10 9l-3 3M14 9l3 3M10 17h4"/></svg><h3>Blockchain business solutions</h3><p>Lorem ipsum dolor sit consectetur adipiscing elit, sed do eiusmod</p></div>
      <div class="eco-item"><svg viewBox="0 0 24 24" fill="none" stroke-width=".9"><path d="M12 4l7 4v8l-7 4-7-4V8z"/><rect x="2" y="2" width="4" height="4"/><rect x="18" y="2" width="4" height="4"/><rect x="2" y="18" width="4" height="4"/><rect x="18" y="18" width="4" height="4"/><text x="12" y="14" font-size="4.5" text-anchor="middle" fill="#0d2a5c" stroke="none" font-family="Poppins,sans-serif" font-weight="600">NFT</text></svg><h3>NFT</h3><p>Lorem ipsum dolor sit consectetur adipiscing elit, sed do eiusmod tempor incididunt ut</p></div>
    </div>
    <span class="round-arrow round-arrow--next"><svg viewBox="0 0 10 10" fill="none" stroke-width=".8"><path d="M4 3l2 2-2 2"/></svg></span>
    <div class="pixel-art" style="right:0;bottom:0;width:36px;height:48px;background:linear-gradient(180deg,#c9461c,#6a3018)" role="img" aria-label="Pixel-art character with orange hair and sunglasses"></div>
  </section>

  <section class="education">
    <div class="edu-photo" role="img" aria-label="Blue-tinted photo of a person studying at a desk"></div>
    <h2 class="sec-title">Digital Asset <b>Education</b></h2>
    <p class="sec-text">Lorem ipsum dolor sit amet, consectetur adipiscing elit, sed do eiusmod tempor incididunt ut labore et dolore magna aliqua. Ut enim ad minim veniam, quis nostrud exercitation ullamco laboris nisi ut aliquip ex ea commodo consequat. Duis aute irure dolor in reprehenderit in voluptate velit esse cillum</p>
    <div class="edu-actions"><span class="btn btn--red">SIGNUP</span><span class="btn btn--line">BLOG</span></div>
  </section>

  <section class="nft">
    <h2 class="sec-title"><b>NFT Virtaul</b> Module</h2>
    <p class="sec-text">Lorem ipsum dolor sit amet, consectetur adipiscing elit, sed do eiusmod tempor incididunt ut labore et dolore magna aliqua. Ut enim ad minim veniam, quis nostrud</p>
    <div class="nft-row">
      <article class="nft-card"><div class="nft-media" style="background:#e3e4e6" role="img" aria-label="Pixel-art character in a red hat on a grey background"></div><h3>Art</h3><p>Lorem ipsum dolor sit adipiscing elit, sed do incididunt ut labore et Lorem ipsum dolor sit consectetur</p><span class="btn btn--navy">Read More</span></article>
      <article class="nft-card"><div class="nft-media" style="background:linear-gradient(135deg,#2a1a6e,#7a2aa8 55%,#c04bc4)" role="img" aria-label="Purple music-themed illustration with musical notes"></div><h3>Music</h3><p>Lorem ipsum dolor sit adipiscing elit, sed do incididunt ut labore et Lorem ipsum dolor sit consectetur</p><span class="btn btn--navy">Read More</span></article>
      <article class="nft-card"><div class="nft-media" style="background:linear-gradient(180deg,#6b7da8,#e3a07a 45%,#2f4a5a)" role="img" aria-label="Gaming illustration of a figure facing a glowing sky among ruins"></div><h3>Gaming</h3><p>Lorem ipsum dolor sit adipiscing elit, sed do incididunt ut labore et Lorem ipsum dolor sit consectetur</p><span class="btn btn--navy">Read More</span></article>
    </div>
    <div class="pixel-art" style="left:0;bottom:0;width:20px;height:38px;background:linear-gradient(180deg,#3b5a30,#5c8a45)" role="img" aria-label="Pixel-art green zombie character"></div>
  </section>

  <section class="tutorial">
    <h2 class="sec-title">Tutorial</h2>
    <div class="tut-row">
      <article class="tut-card"><div class="tut-media" style="background:linear-gradient(135deg,#6b5346,#a87a62 50%,#3c2d27)" role="img" aria-label="Video thumbnail of a man writing at a desk"><span class="play"></span></div><h3>Lorem ipsum dolor sit amet, adipiscing elit, sed do Lorem ipsum</h3><p>Lorem ipsum dolor sit amet, adipiscing elit, sed do eiusmod tempor incididunt</p><div class="tut-meta"><span>$20.00 <s>$25.00</s></span><span class="socials"><span>Chirplo</span><span>Snapmora</span></span></div></article>
      <article class="tut-card"><div class="tut-media" style="background:linear-gradient(135deg,#3d5a82,#6f8fb5 50%,#2a3a55)" role="img" aria-label="Video thumbnail of a woman working on a laptop"><span class="play"></span></div><h3>Lorem ipsum dolor sit amet, adipiscing elit, sed do Lorem ipsum</h3><p>Lorem ipsum dolor sit amet, adipiscing elit, sed do eiusmod tempor incididunt</p><div class="tut-meta"><span>Free</span><span class="socials"><span>Huddlex</span><span>Wirepost</span></span></div></article>
      <article class="tut-card"><div class="tut-media" style="background:linear-gradient(135deg,#4a4f57,#7a7f87 50%,#2e3137)" role="img" aria-label="Video thumbnail of a laptop with floating interface icons"><span class="play"></span></div><h3>Lorem ipsum dolor sit amet, adipiscing elit, sed do Lorem ipsum</h3><p>Lorem ipsum dolor sit amet, adipiscing elit, sed do eiusmod tempor incididunt</p><div class="tut-meta"><span>$20.00</span><span class="socials"><span>Chirplo</span><span>Huddlex</span></span></div></article>
    </div>
  </section>

  <section class="newsletter">
    <h2 class="sec-title">Newsletter</h2>
    <p class="sec-text">Lorem ipsum dolor sit amet, consectetur adipiscing elit, sed do eiusmod tempor incididunt ut labore et dolore magna aliqua.</p>
    <div class="news-form"><span class="news-input">Please enter your email</span><span class="news-btn">SUBSCRIBE NOW</span></div>
  </section>

  <footer class="site-footer">
    <div class="foot-col foot-col--links"><h4>QUICK LINKS</h4><p>Home</p><p>About Us</p><p>PHR Ecosystem</p><p>Blog</p><p>Contact</p></div>
    <div class="foot-col foot-col--eco"><h4>PHR ECOSYSTEM</h4><p>Crypto News</p><p>Digital asset investing</p><p>Blockchain business solutions</p><p>NFT Creative art Projects</p></div>
    <div class="foot-col foot-col--contact"><h4>CONTACT US</h4>
      <p class="label">ADDRESS</p><p class="line"><svg viewBox="0 0 10 10"><path d="M5 0a3.5 3.5 0 0 0-3.5 3.5C1.5 6 5 10 5 10s3.5-4 3.5-6.5A3.5 3.5 0 0 0 5 0zm0 5a1.5 1.5 0 1 1 0-3 1.5 1.5 0 0 1 0 3z"/></svg><span>Lorem ipsum dolor sit amet, consectetur adipiscing</span></p>
      <p class="label">PHONE</p><p class="line"><svg viewBox="0 0 10 10"><path d="M2 0l2 2-1 2c1 1.5 2 2.5 3 3l2-1 2 2-1.5 2C4 10 0 6 0 1.5z"/></svg><span>+1 555-010-0199</span></p>
      <p class="label">EMAIL</p><p class="line"><svg viewBox="0 0 10 10"><path d="M0 2h10v6H0zM1 3l4 3 4-3" fill="none" stroke="currentColor" stroke-width="1"/></svg><span>info@PixelHarborRangers.com</span></p>
    </div>
    <div class="foot-col foot-col--news"><h4>NEWSLETTER</h4><p style="line-height:7px">Lorem ipsum dolor sit amet, consectetur adipiscing elit, sed do eiusmod tempor</p><div class="foot-input"><span>Enter Email</span><i></i></div></div>
  </footer>
  <div class="bottom-bar">
    <span class="copyright">© 2022 &nbsp;All Rights Reserved</span>
    <div class="pay-row"><span>Paylo</span><span>Cardix</span><span>Tendra</span><span>Voucha</span><span>Remitto</span></div>
    <div class="socials"><span>Chirplo</span><span>Snapmora</span><span>Huddlex</span><span>Wirepost</span></div>
  </div>
</main>

<main class="panel panel--right theme-dark">
  <header class="hero">
    <div class="hero-photo" role="img" aria-label="Photo of a smiling man in glasses and a denim jacket working at a laptop in a café"></div>
    <div class="logo">PixelHarbor Rangers</div>
    <div class="account">
      <span><i class="ring"><svg width="5" height="5" viewBox="0 0 10 10" fill="#fff"><circle cx="5" cy="3" r="2"/><path d="M1 10c0-3 2-4 4-4s4 1 4 4z"/></svg></i>LOGIN</span>
      <span><i class="ring"><svg width="5" height="5" viewBox="0 0 10 10" fill="#fff"><path d="M0 1h2l1 5h6l1-4H3"/><circle cx="4" cy="8.5" r="1"/><circle cx="8" cy="8.5" r="1"/></svg></i>CART</span>
    </div>
    <div class="rule"></div>
    <nav class="nav"><span>HOME</span><i>|</i><span>ABOUT US</span><i>|</i><span>PHR ECOSYSTEM</span><i>|</i><span>BLOG</span><i>|</i><span>CONTACT</span></nav>
    <div class="socials"><span>Chirplo</span><span>Snapmora</span><span>Huddlex</span><span>Wirepost</span></div>
    <div class="hero-band">
      <svg class="arrow arrow--prev" viewBox="0 0 10 6" fill="none" stroke="#fff" stroke-width="1"><path d="M10 3H1M3 1L1 3l2 2"/></svg>
      <h1 class="hero-title">PixelHarbor Rangers</h1>
      <p class="hero-sub">Lorem ipsum dolor sit amet, consectetur adipiscing elit, sed do eiusmod tempor incididunt ut labore et dolore magna aliqua.</p>
      <div class="hero-actions"><span class="btn btn--red">GET STARTED</span><span class="btn btn--line">CONTACT US</span></div>
      <svg class="arrow arrow--next" viewBox="0 0 10 6" fill="none" stroke="#fff" stroke-width="1"><path d="M0 3h9M7 1l2 2-2 2"/></svg>
    </div>
  </header>

  <section class="ecosystem">
    <div class="pixel-art" style="right:0;top:58px;width:60px;height:116px;background:linear-gradient(180deg,#1b1b1b,#262220)" role="img" aria-label="Large faint pixel-art character in the background"></div>
    <h2 class="sec-title"><b>PHR</b> Ecosystem</h2>
    <p class="sec-text">Lorem ipsum dolor sit amet, consectetur adipiscing elit, sed do eiusmod tempor incididunt ut labore et dolore magna aliqua. Ut enim ad minim veniam, quis nostrud</p>
    <span class="round-arrow round-arrow--prev"><svg viewBox="0 0 10 10" fill="none" stroke-width=".8"><path d="M6 3L4 5l2 2"/></svg></span>
    <div class="eco-row">
      <div class="eco-item"><svg viewBox="0 0 24 24" fill="none" stroke-width=".9"><circle cx="11" cy="10" r="7"/><circle cx="11" cy="10" r="4.5"/><circle cx="15" cy="16" r="5"/><path d="M13 18l4-4"/></svg><h3>Crypto News</h3><p>Lorem ipsum dolor sit consectetur adipiscing elit, sed do eiusmod tempor incididunt ut</p></div>
      <div class="eco-item eco-item--active"><svg viewBox="0 0 24 24" fill="none" stroke-width=".9"><rect x="2" y="5" width="15" height="12"/><path d="M4 15v-3M7 15v-5M10 15v-4M4 10l4-3 3 2 5-4"/><circle cx="17" cy="16" r="4"/><circle cx="17" cy="16" r="2"/></svg><h3>Digital asset investing</h3><p>Lorem ipsum dolor sit consectetur adipiscing elit, sed do eiusmod tempor incididunt ut</p></div>
      <div class="eco-item"><svg viewBox="0 0 24 24" fill="none" stroke-width=".9"><path d="M12 2l4 2v4l-4 2-4-2V4z"/><path d="M6 12l4 2v4l-4 2-4-2v-4z"/><path d="M18 12l4 2v4l-4 2-4-2v-4z"/><path d="M10 9l-3 3M14 9l3 3M10 17h4"/></svg><h3>Blockchain business solutions</h3><p>Lorem ipsum dolor sit consectetur adipiscing elit, sed do eiusmod</p></div>
      <div class="eco-item"><svg viewBox="0 0 24 24" fill="none" stroke-width=".9"><path d="M12 4l7 4v8l-7 4-7-4V8z"/><rect x="2" y="2" width="4" height="4"/><rect x="18" y="2" width="4" height="4"/><rect x="2" y="18" width="4" height="4"/><rect x="18" y="18" width="4" height="4"/><text x="12" y="14" font-size="4.5" text-anchor="middle" fill="#fff" stroke="none" font-family="Poppins,sans-serif" font-weight="600">NFT</text></svg><h3>NFT</h3><p>Lorem ipsum dolor sit consectetur adipiscing elit, sed do eiusmod tempor incididunt ut</p></div>
    </div>
    <span class="round-arrow round-arrow--next"><svg viewBox="0 0 10 10" fill="none" stroke-width=".8"><path d="M4 3l2 2-2 2"/></svg></span>
  </section>

  <section class="education">
    <div class="edu-photo" role="img" aria-label="Blue-tinted photo of a person studying at a desk"></div>
    <h2 class="sec-title">Digital Asset <b>Education</b></h2>
    <p class="sec-text">Lorem ipsum dolor sit amet, consectetur adipiscing elit, sed do eiusmod tempor incididunt ut labore et dolore magna aliqua. Ut enim ad minim veniam, quis nostrud exercitation ullamco laboris nisi ut aliquip ex ea commodo consequat. Duis aute irure dolor in reprehenderit in voluptate velit esse cillum</p>
    <div class="edu-actions"><span class="btn btn--red">SIGNUP</span><span class="btn btn--line">BLOG</span></div>
  </section>

  <section class="nft">
    <div class="pixel-art" style="left:10px;top:-26px;width:54px;height:54px;background:linear-gradient(180deg,#7d2226,#4a1416)" role="img" aria-label="Pixel-art red robot character"></div>
    <h2 class="sec-title"><b>NFT Virtaul</b> Module</h2>
    <p class="sec-text">Lorem ipsum dolor sit amet, consectetur adipiscing elit, sed do eiusmod tempor incididunt ut labore et dolore magna aliqua. Ut enim ad minim veniam, quis nostrud</p>
    <div class="nft-row">
      <article class="nft-card"><div class="nft-media" style="background:#e3e4e6" role="img" aria-label="Pixel-art character in a red hat on a grey background"></div><h3>Art</h3><p>Lorem ipsum dolor sit adipiscing elit, sed do incididunt ut labore et Lorem ipsum dolor sit consectetur</p><span class="btn btn--navy">Read More</span></article>
      <article class="nft-card"><div class="nft-media" style="background:linear-gradient(135deg,#2a1a6e,#7a2aa8 55%,#c04bc4)" role="img" aria-label="Purple music-themed illustration with musical notes"></div><h3>Music</h3><p>Lorem ipsum dolor sit adipiscing elit, sed do incididunt ut labore et Lorem ipsum dolor sit consectetur</p><span class="btn btn--navy">Read More</span></article>
      <article class="nft-card"><div class="nft-media" style="background:linear-gradient(180deg,#6b7da8,#e3a07a 45%,#2f4a5a)" role="img" aria-label="Gaming illustration of a figure facing a glowing sky among ruins"></div><h3>Gaming</h3><p>Lorem ipsum dolor sit adipiscing elit, sed do incididunt ut labore et Lorem ipsum dolor sit consectetur</p><span class="btn btn--navy">Read More</span></article>
    </div>
  </section>

  <section class="tutorial">
    <h2 class="sec-title">Tutorial</h2>
    <div class="tut-row">
      <article class="tut-card"><div class="tut-media" style="background:linear-gradient(135deg,#6b5346,#a87a62 50%,#3c2d27)" role="img" aria-label="Video thumbnail of a man writing at a desk"><span class="play"></span></div><h3>Lorem ipsum dolor sit amet, adipiscing elit, sed do Lorem ipsum</h3><p>Lorem ipsum dolor sit amet, adipiscing elit, sed do eiusmod tempor incididunt</p><div class="tut-meta"><span>$20.00 <s>$25.00</s></span><span class="socials"><span>Chirplo</span><span>Snapmora</span></span></div></article>
      <article class="tut-card"><div class="tut-media" style="background:linear-gradient(135deg,#3d5a82,#6f8fb5 50%,#2a3a55)" role="img" aria-label="Video thumbnail of a woman working on a laptop"><span class="play"></span></div><h3>Lorem ipsum dolor sit amet, adipiscing elit, sed do Lorem ipsum</h3><p>Lorem ipsum dolor sit amet, adipiscing elit, sed do eiusmod tempor incididunt</p><div class="tut-meta"><span>Free</span><span class="socials"><span>Huddlex</span><span>Wirepost</span></span></div></article>
      <article class="tut-card"><div class="tut-media" style="background:linear-gradient(135deg,#4a4f57,#7a7f87 50%,#2e3137)" role="img" aria-label="Video thumbnail of a laptop with floating interface icons"><span class="play"></span></div><h3>Lorem ipsum dolor sit amet, adipiscing elit, sed do Lorem ipsum</h3><p>Lorem ipsum dolor sit amet, adipiscing elit, sed do eiusmod tempor incididunt</p><div class="tut-meta"><span>$20.00</span><span class="socials"><span>Chirplo</span><span>Huddlex</span></span></div></article>
    </div>
  </section>

  <section class="newsletter">
    <div class="pixel-art" style="right:4px;top:18px;width:44px;height:44px;background:linear-gradient(180deg,#7d2226,#4a1416)" role="img" aria-label="Pixel-art red robot character"></div>
    <h2 class="sec-title">Newsletter</h2>
    <p class="sec-text">Lorem ipsum dolor sit amet, consectetur adipiscing elit, sed do eiusmod tempor incididunt ut labore et dolore magna aliqua.</p>
    <div class="news-form"><span class="news-input">Please enter your email</span><span class="news-btn">SUBSCRIBE NOW</span></div>
  </section>

  <footer class="site-footer">
    <div class="foot-col foot-col--links"><h4>QUICK LINKS</h4><p>Home</p><p>About Us</p><p>PHR Ecosystem</p><p>Blog</p><p>Contact</p></div>
    <div class="foot-col foot-col--eco"><h4>PHR ECOSYSTEM</h4><p>Crypto News</p><p>Digital asset investing</p><p>Blockchain business solutions</p><p>NFT Creative art Projects</p></div>
    <div class="foot-col foot-col--contact"><h4>CONTACT US</h4>
      <p class="label">ADDRESS</p><p class="line"><svg viewBox="0 0 10 10"><path d="M5 0a3.5 3.5 0 0 0-3.5 3.5C1.5 6 5 10 5 10s3.5-4 3.5-6.5A3.5 3.5 0 0 0 5 0zm0 5a1.5 1.5 0 1 1 0-3 1.5 1.5 0 0 1 0 3z"/></svg><span>Lorem ipsum dolor sit amet, consectetur adipiscing</span></p>
      <p class="label">PHONE</p><p class="line"><svg viewBox="0 0 10 10"><path d="M2 0l2 2-1 2c1 1.5 2 2.5 3 3l2-1 2 2-1.5 2C4 10 0 6 0 1.5z"/></svg><span>+1 555-010-0199</span></p>
      <p class="label">EMAIL</p><p class="line"><svg viewBox="0 0 10 10" style="color:#fff"><path d="M0 2h10v6H0zM1 3l4 3 4-3" fill="none" stroke="currentColor" stroke-width="1"/></svg><span>info@PixelHarborRangers.com</span></p>
    </div>
    <div class="foot-col foot-col--news"><h4>NEWSLETTER</h4><p style="line-height:7px">Lorem ipsum dolor sit amet, consectetur adipiscing elit, sed do eiusmod tempor</p><div class="foot-input"><span>Enter Email</span><i></i></div></div>
  </footer>
  <div class="bottom-bar">
    <span class="copyright">© 2022 &nbsp;All Rights Reserved</span>
    <div class="pay-row"><span>Paylo</span><span>Cardix</span><span>Tendra</span><span>Voucha</span><span>Remitto</span></div>
    <div class="socials"><span>Chirplo</span><span>Snapmora</span><span>Huddlex</span><span>Wirepost</span></div>
  </div>
</main>

</body>
</html>
```